A clean crisp business card for a Landscape Construction company. Designed to be easy to read contact/ info and also be appealing/interesting, unlike a traditional business card.

Industry/Entity Type

Landscape Construction

Contact Information for Business Card

Company name : Brambleford Landscape Construction, phone number: (877) 62Vista, website:Bramblefordyards.example, Email, sales@bramblefordyards.example

Requirements
Nice to have
• Luxurious finishes/ details…. Icons or emblems next to contact info
Should not have
• Clipart or general pictures

```html
<!DOCTYPE html>
<html lang="en">
<head>
<meta charset="utf-8">
<title>Brambleford Landscape Construction – Business Card</title>
<link href="https://fonts.googleapis.com/css2?family=Montserrat:wght@300;700&family=Ubuntu:wght@400;500&display=swap" rel="stylesheet">
<style>
  :root {
    --navy: #14286e;
    --royal: #1f6bb5;
    --text-blue: #1d57a6;
    --cyan: #1bb6ea;
    --teal: #0490d2;
    --green: #a0c846;
    --rule: #e6edf3;
    --white: #ffffff;
  }
  * { margin: 0; padding: 0; box-sizing: border-box; }
  html, body { width: 1200px; height: 348px; overflow: hidden; background: var(--white); }
  .sheet { position: relative; width: 1200px; height: 348px; }
  .sheet__field { position: absolute; inset: 0; }
  .front, .back { position: absolute; top: 0; height: 348px; }
  .front { left: 0; width: 575px; }
  .back { left: 575px; width: 625px; }

  .holder { position: absolute; left: 43px; top: 82px; }
  .holder__name {
    font-family: "Montserrat", sans-serif; font-weight: 700;
    font-size: 24px; color: var(--navy); letter-spacing: 0.5px; line-height: 1;
  }
  .holder__role {
    font-family: "Montserrat", sans-serif; font-weight: 300;
    font-size: 17px; color: var(--cyan); letter-spacing: 4.3px;
    margin-left: 7px; margin-top: 2px; line-height: 1;
  }

  .contacts { position: absolute; left: 43px; top: 0; list-style: none; }
  .contact {
    position: absolute; left: 0; display: flex; align-items: center;
    width: 340px; font-family: "Ubuntu", sans-serif; font-size: 13.6px;
    color: var(--text-blue); line-height: 15.5px; white-space: nowrap;
  }
  .contact__icon { width: 28px; height: 28px; flex: none; margin-right: 9px; }
  .contact--address { top: 164px; }
  .contact--web { top: 200px; }
  .contact--mail { top: 237px; }
  .contact--phone { top: 276px; }

  .brand {
    position: absolute; left: 0; top: 84px; width: 422px;
    display: flex; flex-direction: column; align-items: center;
    font-family: "Ubuntu", sans-serif; font-weight: 500; color: var(--royal);
  }
  .brand__mark { width: 44px; height: 44px; border-radius: 50%; background: var(--royal); margin-bottom: 16px; }
  .brand__name { font-size: 34px; line-height: 1; }
  .brand__line { font-size: 14px; line-height: 1; margin-top: 9px; }
</style>
</head>
<body>
<main class="sheet">
  <svg class="sheet__field" viewBox="0 0 1200 348" width="1200" height="348">
    <defs>
      <linearGradient id="field-front" x1="0" y1="0" x2="1" y2="0.3">
        <stop offset="0.2" stop-color="var(--royal)"/>
        <stop offset="0.6" stop-color="var(--teal)"/>
        <stop offset="1" stop-color="var(--green)"/>
      </linearGradient>
      <linearGradient id="field-back" x1="0" y1="0" x2="1" y2="0.2">
        <stop offset="0.3" stop-color="var(--royal)"/>
        <stop offset="0.7" stop-color="var(--teal)"/>
        <stop offset="1" stop-color="var(--green)"/>
      </linearGradient>
    </defs>
    <g role="img" aria-label="Decorative sweeping wave artwork in blue, teal and green">
      <path d="M102,3 C220,25 280,110 340,185 C395,255 420,310 460,348 L575,348 L575,3 Z" fill="url(#field-front)"/>
    </g>
    <g role="img" aria-label="Decorative sweeping wave artwork in blue, teal and green">
      <path d="M827,348 C900,340 950,300 1010,228 C1080,135 1125,50 1184,3 L1200,3 L1200,348 Z" fill="url(#field-back)"/>
    </g>
    <line x1="670" y1="298" x2="869" y2="298" stroke="var(--rule)" stroke-width="1"/>
    <line x1="883" y1="298" x2="929" y2="298" stroke="var(--rule)" stroke-width="1"/>
  </svg>

  <section class="front">
    <div class="holder">
      <h1 class="holder__name">YOUR NAME</h1>
      <p class="holder__role">your position</p>
    </div>
    <ul class="contacts">
      <li class="contact contact--address">
        <svg class="contact__icon" viewBox="0 0 28 28" aria-hidden="true"><circle cx="14" cy="14" r="14" fill="var(--navy)"/><path d="M14 6.5a5 5 0 0 0-5 5c0 3.7 5 9.5 5 9.5s5-5.8 5-9.5a5 5 0 0 0-5-5z" fill="#fff"/><circle cx="14" cy="11.5" r="1.8" fill="var(--navy)"/></svg>
        <span>4127 Alder Hollow Rd., Suite 118,<br>Marlow Falls, OH 45210</span>
      </li>
      <li class="contact contact--web">
        <svg class="contact__icon" viewBox="0 0 28 28" aria-hidden="true"><circle cx="14" cy="14" r="14" fill="var(--royal)"/><g fill="none" stroke="#fff" stroke-width="1.4"><circle cx="14" cy="14" r="7.5"/><ellipse cx="14" cy="14" rx="3.4" ry="7.5"/><line x1="6.5" y1="14" x2="21.5" y2="14"/><line x1="7.8" y1="10.3" x2="20.2" y2="10.3"/><line x1="7.8" y1="17.7" x2="20.2" y2="17.7"/></g></svg>
        <span>bramblefordyards.example</span>
      </li>
      <li class="contact contact--mail">
        <svg class="contact__icon" viewBox="0 0 28 28" aria-hidden="true"><circle cx="14" cy="14" r="14" fill="#1a74c0"/><g fill="none" stroke="#fff" stroke-width="1.4"><rect x="6.5" y="9" width="15" height="10"/><path d="M6.5 9l7.5 6 7.5-6M6.5 19l5.5-5M21.5 19l-5.5-5"/></g></svg>
        <span>sales@bramblefordyards.example</span>
      </li>
      <li class="contact contact--phone">
        <svg class="contact__icon" viewBox="0 0 28 28" aria-hidden="true"><circle cx="14" cy="14" r="14" fill="var(--cyan)"/><path d="M9.6 7.2l2.3-.4 1.4 3.4-1.6 1.3c.8 1.8 2.1 3.2 3.9 4.1l1.3-1.6 3.4 1.4-.4 2.3c-.2.8-.9 1.3-1.7 1.2C12.4 18.4 9 14.9 8.4 9c-.1-.8.4-1.6 1.2-1.8z" fill="#fff"/></svg>
        <span>(877) 62Vista</span>
      </li>
    </ul>
  </section>

  <section class="back">
    <div class="brand">
      <span class="brand__mark" aria-hidden="true"></span>
      <p class="brand__name">Brambleford</p>
      <p class="brand__line">Landscape Construction</p>
    </div>
  </section>
</main>
</body>
</html>
```